Stonebrace Business Card Design

The Stonebrace Co is an aggregate (crushing) equipment dealer serving Western Canadian provinces. Stonebrace is a distributor of aggregate equipment for different manufacturers.

We are looking to change and update the existing business card which has been used since the existence of the company. A copy of existing card has been attached for reference. The Stonebrace Co logo we want to remain the same and we want the green color to remain the same.

We are wanting something new with a different look. A refreshing card to show a new modern and updated look. No longer wanting to have the manufacturers on the back of the card but something more like our logo on the back of the card with a statement like "Crushing Solutions"

ideas could be:
- card can be different colors on front and back
- front or reverse of the card could possibly be the green color with the logo in black

Target Market(s)

Owners of Aggregate/Crushing companies

Contact Information for Business Card

see above

Requirements
Must have
• - logo to remain same along with same font within logo
• - green color to remain same
Nice to have
• as noted above under project description
Should not have

```html
<!DOCTYPE html>
<html lang="en">
<head>
<meta charset="utf-8">
<title>Stonebrace Business Card</title>
<link href="https://fonts.googleapis.com/css2?family=Roboto:wght@400;500;700&family=Roboto+Condensed:wght@700&display=swap" rel="stylesheet">
<style>
  :root {
    --brand-green: #878a09;
    --ink: #231f20;
    --text-grey: #4a4a4a;
    --card-white: #f3f3f3;
    --rule-grey: #8c8c8c;
    --backdrop: #6b4a35;
  }
  * { margin: 0; padding: 0; box-sizing: border-box; }
  html, body { width: 1200px; height: 960px; overflow: hidden; }
  body {
    background: var(--backdrop);
    font-family: "Roboto", Arial, sans-serif;
    position: relative;
  }
  .card {
    position: absolute;
    left: 320px;
    width: 600px;
    border-radius: 20px;
    overflow: hidden;
  }
  /* Front face */
  .card-front {
    top: 95px;
    height: 355px;
    background: var(--brand-green);
    color: var(--ink);
  }
  .front-wordmark {
    position: absolute;
    left: 0; right: 0;
    top: 100px;
    height: 160px;
    display: flex;
    justify-content: center;
    align-items: center;
    gap: 18px;
    font-weight: 700;
    font-size: 36px;
    letter-spacing: 0.3px;
    white-space: nowrap;
  }
  .mark-dot {
    flex: none;
    width: 48px; height: 48px;
    border-radius: 50%;
    background: var(--ink);
  }
  .front-tagline {
    position: absolute;
    left: 0; right: 0;
    top: 304px;
    text-align: center;
    font-weight: 700;
    font-size: 14px;
  }
  /* Back face */
  .card-back {
    top: 493px;
    height: 342px;
    background: var(--card-white);
  }
  .back-wordmark {
    position: absolute;
    left: 40px;
    width: 290px;
    top: 80px;
    height: 140px;
    display: flex;
    justify-content: center;
    align-items: center;
    gap: 12px;
    font-weight: 700;
    font-size: 23px;
    color: var(--ink);
    white-space: nowrap;
  }
  .back-wordmark .mark-dot { width: 32px; height: 32px; background: var(--brand-green); }
  .divider {
    position: absolute;
    left: 342px;
    top: 55px;
    width: 1px;
    height: 200px;
    background: #c9c9c9;
  }
  .contact {
    position: absolute;
    left: 371px;
    top: 55px;
  }
  .contact-name {
    font-family: "Roboto Condensed", Arial, sans-serif;
    font-weight: 700;
    font-size: 21px;
    color: var(--brand-green);
    line-height: 24px;
  }
  .contact-role {
    font-weight: 500;
    font-size: 14px;
    color: var(--ink);
    line-height: 20px;
  }
  .contact-address {
    margin-top: 8px;
    font-size: 14px;
    color: var(--text-grey);
    line-height: 19px;
  }
  .contact-lines {
    margin-top: 10px;
    list-style: none;
    font-size: 14px;
    color: var(--text-grey);
    line-height: 19px;
  }
  .contact-lines li { display: flex; align-items: center; gap: 9px; }
  .contact-lines svg { width: 13px; height: 13px; fill: var(--text-grey); }
  .web-band {
    position: absolute;
    left: 0; right: 0;
    top: 293px;
    height: 34px;
    border-top: 2px solid var(--rule-grey);
    border-bottom: 2px solid var(--rule-grey);
    background: var(--brand-green);
    color: #ffffff;
    font-size: 14px;
    letter-spacing: 7px;
    text-align: center;
    line-height: 30px;
  }
</style>
</head>
<body>

<section class="card card-front" aria-label="Card front">
  <div class="front-wordmark"><span class="mark-dot"></span><span>THE STONEBRACE CO.</span></div>
  <p class="front-tagline">Crushing Solutions</p>
</section>

<section class="card card-back" aria-label="Card back">
  <div class="back-wordmark"><span class="mark-dot"></span><span>THE STONEBRACE CO.</span></div>
  <div class="divider"></div>
  <div class="contact">
    <p class="contact-name">DALE MORROW</p>
    <p class="contact-role">CEO/FOUNDER</p>
    <p class="contact-address">2280- 48B Avenue<br>Nisku, Alberta T9E 1K2</p>
    <ul class="contact-lines">
      <li><svg viewBox="0 0 16 16"><path d="M3 1l3 3-1.5 2a9 9 0 005.5 5.5L12 10l3 3-2 2C7 15 1 9 1 3z"/></svg>780.555.0142</li>
      <li><svg viewBox="0 0 16 16"><path d="M4 0h8v16H4zM5.5 2v10h5V2z"/></svg>780.555.0187</li>
      <li><svg viewBox="0 0 16 16"><path d="M4 1h8v4H4zM1 6h14v6h-3v3H4v-3H1zM5 10v3h6v-3z"/></svg>780.555.0163</li>
      <li><svg viewBox="0 0 16 16"><path d="M1 3h14v10H1zM2.5 4.5L8 9l5.5-4.5v-0.2H2.5z"/></svg>dale@stonebr.com</li>
      <li><svg viewBox="0 0 16 16"><circle cx="8" cy="8" r="7"/></svg>www.stonebrace.ca</li>
    </ul>
  </div>
  <div class="web-band">www.stonebrace.ca</div>
</section>

</body>
</html>
```